Newsletter template

I am looking for 2 newsletter templates. My website is in Wordpress and I want to use in mailchimp for lists.

One newsletter is for local clients of design remodeling firm to be sent monthly

Second newsletter is for web store offerings to be sent weekly.

Target Market(s)

Luxury home and leisure

Industry/Entity Type

Store

Requirements
Must have
• Use logos and colors to seamlessly integrate with website,

```html
<!DOCTYPE html>
<html lang="en">
<head>
<meta charset="utf-8">
<title>Marlowe Reid Home – Newsletter</title>
<link rel="stylesheet" href="https://fonts.googleapis.com/css2?family=Open+Sans:wght@400;600&family=Arimo:wght@400;700&display=swap">
<style>
  :root {
    --page: #ffffff;
    --ink: #6b6b6b;
    --accent: #1a9cc4;
    --accent-bar: #5aa6cc;
    --button-blue: #33b5ee;
    --tag-yellow: #dcdc00;
    --button-grey: #a9a9a9;
    --button-grey-dark: #858585;
    --tab-dark: #3e3e3e;
    --photo: #444444;
    --rule: #e2e2e2;
  }
  * { margin: 0; padding: 0; box-sizing: border-box; }
  html, body { width: 698px; height: 1200px; overflow: hidden; background: var(--page); }
  .newsletter {
    position: relative; width: 750px; height: 1290px;
    transform: scale(0.9307); transform-origin: 0 0;
    font-family: "Arimo", Arial, sans-serif; color: var(--ink);
  }
  .abs { position: absolute; }

  .issue-tab {
    left: 57px; top: 0; width: 196px; height: 70px;
    background: var(--tab-dark);
    color: #fff; font-family: "Open Sans", sans-serif; font-size: 18px;
    text-align: center; line-height: 76px;
  }

  .utility-links { right: 63px; top: 8px; font-size: 11px; color: var(--ink); }
  .utility-links a { color: var(--accent); text-decoration: none; }

  .brand { left: 0; width: 750px; top: 76px; text-align: center; }
  .brand-name { font-size: 30px; font-weight: 400; color: var(--accent); letter-spacing: 0.5px; }

  .divider {
    left: 57px; width: 630px; height: 10px;
    background: radial-gradient(ellipse at center, #cfcfcf 0%, #ececec 45%, rgba(255,255,255,0) 72%);
    border-top: 1px dotted #e0e0e0;
  }

  .photo { background: var(--photo); }

  .feature-bar { left: 57px; top: 567px; width: 630px; height: 5px; background: var(--accent-bar); }
  .headline { font-size: 18px; font-weight: 400; color: var(--accent); }
  .body-copy { font-size: 12.2px; line-height: 20px; color: var(--ink); }

  .button {
    display: block; color: #fff; font-size: 11px; font-weight: 700;
    text-align: center; letter-spacing: 0.5px; text-transform: uppercase;
    text-decoration: none;
    box-shadow: 0 2px 0 rgba(0,0,0,0.15);
  }
  .button-primary { background: var(--button-blue); width: 99px; height: 22px; line-height: 22px; }
  .button-muted { background: var(--button-grey); width: 64px; height: 22px; line-height: 22px; }
  .button-dark { background: var(--button-grey-dark); width: 64px; height: 22px; line-height: 22px; }

  .tag {
    background: var(--tag-yellow); color: #fff; font-size: 11px; font-weight: 700;
    height: 23px; line-height: 23px; padding: 0 8px; text-transform: uppercase;
  }
  .thin-rule {
    left: 57px; top: 945px; width: 630px; height: 1px;
    background: linear-gradient(90deg, rgba(220,220,220,0), var(--rule) 20%, var(--rule) 80%, rgba(220,220,220,0));
  }
</style>
</head>
<body>
<main class="newsletter">

  <div class="abs issue-tab">newsletter</div>

  <nav class="abs utility-links">
    <a href="#">browser version</a> • <a href="#">text version</a> • <a href="#">unsubscribe</a>
  </nav>

  <header class="abs brand">
    <span class="brand-name">Marlowe Reid Home</span>
  </header>

  <div class="abs divider" style="top:168px"></div>

  <div class="abs photo" style="left:57px;top:197px;width:630px;height:350px" role="img" aria-label="Feature photograph of a luxury interior"></div>

  <div class="abs feature-bar"></div>
  <h1 class="abs headline" style="left:57px;top:592px">Non semper lorem sollicitudin</h1>
  <a class="abs button button-primary" href="#" style="left:588px;top:592px">View more</a>
  <p class="abs body-copy" style="left:57px;top:628px;width:510px">Donec porttitor quam vel purus venenatis rutrum. Nullam quam nibh, congue sed aliquet posuere, aliquam non lacus. Maecenas nec luctus neque. Aliquam sagittis tincidunt lectus, non semper lorem sollicitudin ac. Proin ac felis tortor, eu ultricies orci.</p>

  <div class="abs divider" style="top:712px"></div>

  <article>
    <span class="abs tag" style="left:57px;top:749px">The special one article</span>
    <h2 class="abs headline" style="left:57px;top:788px">Quisque convallis</h2>
    <p class="abs body-copy" style="left:57px;top:820px;width:310px">Donec porttitor quam vel purus venenatis rutrum. Nullam quam nibh, congue sed aliquet posuere, aliquam non lacus. Maecenas nec luctus neque...</p>
    <a class="abs button button-muted" href="#" style="left:57px;top:900px">More</a>
    <div class="abs photo" style="left:382px;top:749px;width:305px;height:172px" role="img" aria-label="Article photograph of a furnished room"></div>
  </article>

  <div class="abs thin-rule"></div>

  <article>
    <span class="abs tag" style="left:57px;top:966px">Flexible</span>
    <h2 class="abs headline" style="left:57px;top:1005px">Sed eu laoreet metus</h2>
    <p class="abs body-copy" style="left:57px;top:1037px;width:310px">Donec porttitor quam vel purus venenatis rutrum. Nullam quam nibh, congue sed aliquet posuere, aliquam non lacus. Maecenas nec luctus neque...</p>
    <a class="abs button button-dark" href="#" style="left:57px;top:1117px">View</a>
    <div class="abs photo" style="left:382px;top:966px;width:305px;height:172px" role="img" aria-label="Article photograph of home décor products"></div>
  </article>

  <div class="abs divider" style="top:1166px"></div>

  <div class="abs photo" style="left:57px;top:1202px;width:630px;height:120px" role="img" aria-label="Wide banner photograph of a luxury living space"></div>

</main>
</body>
</html>
```